Silver Bloom Marisol's Cleaning Service Business Cards Project

A business card with all contact details with logo design on there (already have a logo) eye catching Logo and contact info on one side, full logo on the back, must target upper class residential and corporate companies, fitness companies, still keep it on the feminine side of things , must look elegant

Target Market(s)

Upper class homes and corporate companies

Industry/Entity Type

Cleaning Service

Contact Information for Business Card

Name: Marisol Quenby
Position: Director
ABN: 31647209853
Email: marisolssilvercleaning@tidymail.example
Number: 0417906354

Font styles to use
Decorative

Colors

Designer to choose colors to be used in the design.

Requirements
Must have
• Available Sydney Wide, contact info and logo on one side, full logo on the back
Nice to have
• Professional appearance
Should not have
• Cheap advert looking stuff

```html
<!DOCTYPE html>
<html lang="en">
<head>
<meta charset="utf-8">
<title>Silver Bloom – Business Cards</title>
<link rel="stylesheet" href="https://fonts.googleapis.com/css2?family=Roboto:wght@400;500&display=swap">
<style>
  :root {
    --backdrop: #bdbdbd;
    --card: #2e3240;
    --accent: #2ee6dc;
    --ink-dark: #2e3240;
    --ink-light: #ffffff;
  }
  * { margin: 0; padding: 0; box-sizing: border-box; }
  html, body {
    width: 1200px; height: 960px; overflow: hidden;
    background: var(--backdrop);
    font-family: "Roboto", Arial, sans-serif;
  }
  .canvas { position: relative; width: 1200px; height: 960px; }
  .card {
    position: absolute; width: 600px; height: 343px;
    background: var(--card);
  }
  .card--front { left: 322px; top: 108px; }
  .card--back  { left: 320px; top: 493px; }

  .contact-band {
    position: absolute; left: 0; top: 86px;
    width: 322px; height: 168px;
    background: var(--accent);
    color: var(--ink-dark);
    padding: 22px 0 0 28px;
  }
  .contact-band__name { font-size: 20px; font-weight: 500; line-height: 24px; letter-spacing: 0.2px; }
  .contact-band__role { font-size: 15px; font-weight: 500; line-height: 18px; margin-bottom: 10px; }
  .contact-band__line { font-size: 14px; font-weight: 400; line-height: 20px; }
  .contact-band__line--tight { font-size: 13.5px; }

  .brand {
    position: absolute; text-align: center;
    color: var(--accent); font-weight: 500;
  }
  .brand__mark {
    display: block; margin: 0 auto 12px;
    width: 10px; height: 10px; background: var(--accent);
  }
  .brand--front { left: 360px; top: 180px; width: 230px; }
  .brand--front .brand__name { font-size: 22px; letter-spacing: 1.5px; line-height: 28px; }
  .brand--front .brand__tag { font-size: 9px; letter-spacing: 2px; line-height: 16px; }

  .ornament {
    position: absolute; background: linear-gradient(90deg, rgba(46,230,220,0), rgba(46,230,220,0.35), rgba(46,230,220,0));
    border-radius: 30px;
  }
  .ornament--front { left: 376px; top: 160px; width: 192px; height: 36px; }
  .ornament--back { left: 146px; top: 188px; width: 298px; height: 56px; }

  .brand--back { left: 150px; top: 82px; width: 300px; }
  .brand--back .brand__mark { width: 14px; height: 14px; margin-bottom: 14px; }
  .brand--back .brand__name { font-size: 34px; letter-spacing: 2px; line-height: 40px; }
  .brand--back .brand__tag { font-size: 11px; letter-spacing: 2.5px; line-height: 18px; }

  .web {
    position: absolute; left: 0; width: 600px; top: 288px;
    text-align: center; color: var(--ink-light);
    font-size: 14px; letter-spacing: 3.6px;
  }
</style>
</head>
<body>
<main class="canvas">
  <section class="card card--front">
    <div class="contact-band">
      <p class="contact-band__name">MARISOL QUENBY</p>
      <p class="contact-band__role">DIRECTOR</p>
      <p class="contact-band__line">ABN: 31647209853</p>
      <p class="contact-band__line">0417906354</p>
      <p class="contact-band__line contact-band__line--tight">marisolssilvercleaning@tidymail.example</p>
      <p class="contact-band__line">www.silverbloom.example</p>
    </div>
    <div class="ornament ornament--front" role="img" aria-label="Decorative floral scrollwork flourish"></div>
    <div class="brand brand--front">
      <span class="brand__mark"></span>
      <p class="brand__name">SILVER BLOOM</p>
      <p class="brand__tag">MARISOL'S CLEANING SERVICE</p>
    </div>
  </section>

  <section class="card card--back">
    <div class="brand brand--back">
      <span class="brand__mark"></span>
      <p class="brand__name">SILVER BLOOM</p>
      <p class="brand__tag">MARISOL'S CLEANING SERVICE</p>
    </div>
    <div class="ornament ornament--back" role="img" aria-label="Decorative floral scrollwork flourish"></div>
    <p class="web">www.silverbloom.example</p>
  </section>
</main>
</body>
</html>
```